Quillfern Air Business Card Design

Design new, 2 sides, business cards for a residential and light commercial heating, air conditioning contractor.

Target Market(s)

Homeowners, small businesses

Industry/Entity Type

Business

Contact Information for Business Card

Dominic Westerhall
Phone - 862-415-2736
Email
Address - PO box 518
Brightwater NJ 07912
Website - www.HarborBreezeLLC.example

Requirements
Must have
• logo, company colors, standard size with no die cut, so I can use nova stamp

```html
<!DOCTYPE html>
<html lang="en">
<head>
<meta charset="utf-8">
<title>Quillfern Air Business Card</title>
<link rel="stylesheet" href="https://fonts.googleapis.com/css2?family=Arimo:wght@400;700&display=swap">
<style>
  :root {
    --bg: #3a3a3a;
    --orange: #f7961d;
    --red: #a8223a;
    --white: #ffffff;
    --ink: #ffffff;
  }
  * { margin: 0; padding: 0; box-sizing: border-box; }
  html, body { width: 1200px; height: 950px; overflow: hidden; }
  body {
    background: var(--bg);
    font-family: "Arimo", Arial, sans-serif;
    position: relative;
  }
  .card {
    position: absolute;
    left: 250px;
    width: 700px;
    height: 400px;
    overflow: hidden;
    box-shadow: 0 10px 30px rgba(0,0,0,.45);
  }
  .card--front { top: 50px; background: var(--orange); }
  .card--back { top: 500px; background: var(--white); }

  .brand {
    position: absolute;
    display: flex;
    align-items: center;
    gap: 14px;
    color: var(--red);
    font-weight: 700;
    letter-spacing: .5px;
    white-space: nowrap;
  }
  .brand__dot {
    width: 26px; height: 26px; border-radius: 50%;
    background: var(--red);
    flex: none;
  }
  .card--front .brand {
    left: 0; right: 0; top: 0; bottom: 0;
    justify-content: center;
    font-size: 52px;
  }
  .card--back .brand {
    right: 70px; top: 70px;
    font-size: 40px;
  }
  .card--back .brand__dot { width: 20px; height: 20px; }

  .wave { position: absolute; left: 0; top: 0; width: 700px; height: 400px; }

  .contact {
    position: absolute;
    left: 40px;
    bottom: 22px;
    display: flex;
    color: var(--ink);
  }
  .person__name {
    color: var(--orange);
    font-weight: 700;
    font-size: 18px;
    text-transform: uppercase;
    white-space: nowrap;
  }
  .person__title {
    font-size: 13px;
    text-transform: uppercase;
    margin: 3px 0 8px;
  }
  .lines { list-style: none; font-size: 13px; }
  .lines li { display: flex; align-items: center; gap: 8px; height: 19px; white-space: nowrap; }
  .lines svg { width: 13px; height: 13px; flex: none; }
  .divider {
    width: 1px;
    background: rgba(255,255,255,.8);
    margin: 0 20px;
    align-self: stretch;
  }
  .address { font-size: 13px; line-height: 19px; padding-top: 2px; white-space: nowrap; }
</style>
</head>
<body>

  <section class="card card--front" aria-label="Card front">
    <div class="brand"><span class="brand__dot"></span>Quillfern Air</div>
  </section>

  <section class="card card--back" aria-label="Card back">
    <svg class="wave" viewBox="0 0 700 400" aria-hidden="true">
      <path d="M0,132 C110,180 200,222 350,216 C480,211 600,196 700,200 L700,214 C600,210 480,226 350,230 C200,236 110,196 0,150 Z" fill="var(--orange)"/>
      <path d="M0,150 C110,196 200,236 350,230 C480,226 600,210 700,214 L700,400 L0,400 Z" fill="var(--red)"/>
    </svg>

    <div class="brand"><span class="brand__dot"></span>Quillfern Air</div>

    <div class="contact">
      <div class="person">
        <p class="person__name">Dominic Westerhall</p>
        <p class="person__title">President</p>
        <ul class="lines">
          <li>
            <svg viewBox="0 0 16 16"><path d="M3 1h3l1.5 4-2 1.2a9 9 0 0 0 4.3 4.3L11 8.5l4 1.5v3a2 2 0 0 1-2 2A12 12 0 0 1 1 3a2 2 0 0 1 2-2z" fill="var(--orange)"/></svg>
            862-415-2736
          </li>
          <li>
            <svg viewBox="0 0 16 16"><rect x="4" y="1" width="8" height="14" rx="1.5" fill="none" stroke="var(--orange)" stroke-width="2"/></svg>
            862-415-2740
          </li>
          <li>
            <svg viewBox="0 0 16 16"><rect x="2" y="6" width="12" height="8" fill="var(--orange)"/><rect x="4" y="2" width="8" height="5" fill="none" stroke="var(--orange)" stroke-width="1.5"/></svg>
            862-415-2745
          </li>
          <li>
            <svg viewBox="0 0 16 16"><rect x="1" y="3" width="14" height="10" fill="var(--orange)"/><path d="M1 3l7 6 7-6" fill="none" stroke="var(--red)" stroke-width="1.5"/></svg>
            dominic@quillfernair.example
          </li>
        </ul>
      </div>
      <span class="divider"></span>
      <div class="address">
        <p>PO box 518</p>
        <p>Brightwater NJ 07912</p>
        <p>www.QuillfernAirLLC.example</p>
      </div>
    </div>
  </section>

</body>
</html>
```